Corporate Business Card

Very professional, Modern, Not to busy, include phone address email, website
(253) 617-4930, 18761 52nd Avenue S, Kent, WA 98047, martin@plumlinegroup.com, varkoworks.com

Target Market(s)

Manufacturing

Industry/Entity Type

Aero, machining, manufacturing, Off road racing

Contact Information for Business Card

Phone, address email, website

```html
<!DOCTYPE html>
<html lang="en">
<head>
<meta charset="utf-8">
<title>Varko Works – Business Card</title>
<link href="https://fonts.googleapis.com/css2?family=Saira+Semi+Condensed:wght@400;600&display=swap" rel="stylesheet">
<style>
  :root{
    --page-bg:#2a2420;
    --card-dark:#0b0a0d;
    --card-mid:#1c1b20;
    --card-sheen:#34333a;
    --brand-blue:#2f5597;
    --accent-red:#d9303a;
    --ghost-grey:#4a494f;
    --text-light:#e9e9ec;
  }
  *{margin:0;padding:0;box-sizing:border-box}
  html,body{width:1200px;height:913px;overflow:hidden}
  body{
    background:var(--page-bg);
    font-family:"Saira Semi Condensed",sans-serif;
    display:flex;align-items:center;justify-content:center;gap:48px;
  }
  .card{
    position:relative;width:525px;height:300px;border-radius:30px;overflow:hidden;
    background:linear-gradient(115deg,var(--card-dark) 0%,var(--card-mid) 45%,var(--card-sheen) 62%,var(--card-mid) 80%,var(--card-dark) 100%);
    box-shadow:0 18px 40px rgba(0,0,0,.55);
  }
  /* back side */
  .card-back .brand{
    position:absolute;left:0;right:0;top:112px;text-align:center;
    font-weight:600;font-size:50px;letter-spacing:3px;color:var(--ghost-grey);text-transform:uppercase;
  }
  .card-back .brand-rule{
    position:absolute;left:150px;width:225px;top:184px;height:2px;background:var(--ghost-grey);
  }
  /* front side */
  .card-front .brand{
    position:absolute;right:34px;top:26px;
    font-weight:600;font-size:44px;letter-spacing:3px;color:var(--brand-blue);text-transform:uppercase;line-height:1;
  }
  .card-front .brand-rule{
    position:absolute;right:34px;top:84px;width:300px;height:2px;background:var(--brand-blue);
  }
  .contact{
    position:absolute;left:36px;bottom:30px;list-style:none;
    color:var(--text-light);font-size:17px;letter-spacing:.4px;
  }
  .contact li{display:flex;align-items:center;gap:10px;height:28px}
  .contact svg{width:15px;height:15px;fill:var(--brand-blue);flex:none}
  .contact .divider{height:2px;width:330px;background:var(--accent-red);margin:6px 0 6px}
</style>
</head>
<body>
  <section class="card card-back" aria-label="Card back">
    <div class="brand">Varko Works</div>
    <div class="brand-rule"></div>
  </section>

  <section class="card card-front" aria-label="Card front">
    <div class="brand">Varko Works</div>
    <div class="brand-rule"></div>
    <ul class="contact">
      <li>
        <svg viewBox="0 0 24 24"><path d="M6.6 10.8a15.1 15.1 0 0 0 6.6 6.6l2.2-2.2c.3-.3.7-.4 1-.2 1.1.4 2.3.6 3.6.6.6 0 1 .4 1 1V20c0 .6-.4 1-1 1A17 17 0 0 1 3 4c0-.6.4-1 1-1h3.5c.6 0 1 .4 1 1 0 1.3.2 2.5.6 3.6.1.3 0 .7-.2 1z"/></svg>
        (253) 617-4930
      </li>
      <li>
        <svg viewBox="0 0 24 24"><path d="M12 2a10 10 0 1 0 0 20 10 10 0 0 0 0-20zm6.9 6h-3a15.6 15.6 0 0 0-1.4-3.6A8 8 0 0 1 18.9 8zM12 4c.8 1.2 1.5 2.5 1.9 4h-3.8c.4-1.5 1.1-2.8 1.9-4zM4.3 14a8.2 8.2 0 0 1 0-4h3.4a16.5 16.5 0 0 0 0 4zm.8 2h3a15.6 15.6 0 0 0 1.4 3.6A8 8 0 0 1 5.1 16zm3-8h-3a8 8 0 0 1 4.4-3.6C8.9 5.5 8.4 6.7 8.1 8zM12 20c-.8-1.2-1.5-2.5-1.9-4h3.8c-.4 1.5-1.1 2.8-1.9 4zm2.3-6H9.7a14.7 14.7 0 0 1 0-4h4.6a14.7 14.7 0 0 1 0 4zm.2 5.6c.6-1.1 1.1-2.3 1.4-3.6h3a8 8 0 0 1-4.4 3.6zm1.8-5.6a16.5 16.5 0 0 0 0-4h3.4a8.2 8.2 0 0 1 0 4z"/></svg>
        www.varkoworks.com
      </li>
      <li>
        <svg viewBox="0 0 24 24"><path d="M3 5h18c.6 0 1 .4 1 1v12c0 .6-.4 1-1 1H3c-.6 0-1-.4-1-1V6c0-.6.4-1 1-1zm9 7.2L4.5 7v1.9l7.5 5.2 7.5-5.2V7z"/></svg>
        martin@plumlinegroup.com
      </li>
      <li class="divider" aria-hidden="true"></li>
      <li>
        <svg viewBox="0 0 24 24"><path d="M12 2a7 7 0 0 0-7 7c0 5.2 7 13 7 13s7-7.8 7-13a7 7 0 0 0-7-7zm0 9.5A2.5 2.5 0 1 1 12 6.5a2.5 2.5 0 0 1 0 5z"/></svg>
        18761 52nd Avenue S, Kent, WA 98047
      </li>
    </ul>
  </section>
</body>
</html>
```